Corvane Capital Business Cards

These are professional business cards that are for my family office.
Put fake emails and phone numbers as of now until I finalize those components. This family office controls my families investments, assets, and future. The cards should be professional.
..
.
.
.
I just uploaded another variation of a logo I would like to see as a business card to I am inbeteen which logo to use

Target Market(s)

business

Industry/Entity Type

business

Contact Information for Business Card

Professional, wealth related, finance related.

Requirements
Must have
• Logo

```html
<!DOCTYPE html>
<html lang="en">
<head>
<meta charset="UTF-8">
<title>Corvane Capital – Business Cards</title>
<link href="https://fonts.googleapis.com/css2?family=Poppins:wght@400;500;600&display=swap" rel="stylesheet">
<style>
  :root {
    --backdrop: #e3e8ea;
    --navy: #181d2a;
    --paper: #ffffff;
    --ink: #1a1f2c;
  }
  * { margin: 0; padding: 0; box-sizing: border-box; }
  html, body {
    width: 1200px;
    height: 960px;
    overflow: hidden;
    background: var(--backdrop);
    font-family: "Poppins", sans-serif;
    color: var(--ink);
  }
  .canvas { position: relative; width: 1200px; height: 960px; }
  .card {
    position: absolute;
    left: 250px;
    width: 701px;
    height: 400px;
    border-radius: 24px;
  }
  .card--front { top: 60px; background: var(--navy); }
  .card--back { top: 500px; background: var(--paper); }

  .wordmark {
    position: absolute;
    left: 0; right: 0;
    top: 178px;
    text-align: center;
    font-family: "Poppins", sans-serif;
    font-weight: 500;
    font-size: 36px;
    letter-spacing: 3px;
    text-transform: uppercase;
    color: var(--paper);
  }

  .identity {
    position: absolute;
    right: 402px;
    top: 165px;
    text-align: right;
  }
  .identity__name {
    font-size: 36px;
    line-height: 40px;
    font-weight: 400;
    letter-spacing: 0.3px;
  }
  .identity__name strong { font-weight: 600; }
  .identity__title {
    font-size: 17px;
    font-weight: 600;
    line-height: 22px;
    margin-top: -2px;
  }
  .divider {
    position: absolute;
    left: 349px;
    top: 133px;
    width: 2px;
    height: 134px;
    background: var(--ink);
  }
  .contacts {
    position: absolute;
    left: 399px;
    top: 170px;
    list-style: none;
  }
  .contacts li {
    display: flex;
    align-items: center;
    height: 25.5px;
    font-size: 19px;
    line-height: 1;
  }
  .contacts svg {
    width: 17px;
    height: 17px;
    margin-right: 11px;
    fill: var(--ink);
    flex-shrink: 0;
  }
  .address {
    position: absolute;
    left: 0; right: 0;
    top: 330px;
    text-align: center;
    font-size: 19px;
    padding-right: 28px;
  }
</style>
</head>
<body>
<main class="canvas">
  <section class="card card--front">
    <h1 class="wordmark">Corvane Capital</h1>
  </section>

  <section class="card card--back">
    <div class="identity">
      <p class="identity__name"><strong>Marta</strong> Kovalik</p>
      <p class="identity__title">Founder &amp; CEO</p>
    </div>
    <div class="divider"></div>
    <ul class="contacts">
      <li>
        <svg viewBox="0 0 24 24" aria-hidden="true"><path d="M6.6 10.8a15.1 15.1 0 0 0 6.6 6.6l2.2-2.2a1 1 0 0 1 1-.25 11.4 11.4 0 0 0 3.6.57 1 1 0 0 1 1 1V20a1 1 0 0 1-1 1A17 17 0 0 1 3 4a1 1 0 0 1 1-1h3.5a1 1 0 0 1 1 1c0 1.25.2 2.45.57 3.57a1 1 0 0 1-.25 1z"/></svg>
        (555) 014-2760
      </li>
      <li>
        <svg viewBox="0 0 24 24" aria-hidden="true"><path d="M12 2a10 10 0 1 0 0 20 10 10 0 0 0 0-20zm6.9 6h-2.9a15.6 15.6 0 0 0-1.4-3.6A8 8 0 0 1 18.9 8zM12 4c.8 1.2 1.5 2.5 1.9 4h-3.8c.4-1.5 1.1-2.8 1.9-4zM4.3 14a8 8 0 0 1 0-4h3.4a16.5 16.5 0 0 0 0 4zm.8 2h2.9c.3 1.3.8 2.5 1.4 3.6A8 8 0 0 1 5.1 16zM8 8H5.1a8 8 0 0 1 4.3-3.6C8.8 5.5 8.3 6.7 8 8zm4 12c-.8-1.2-1.5-2.5-1.9-4h3.8c-.4 1.5-1.1 2.8-1.9 4zm2.3-6H9.7a14.7 14.7 0 0 1 0-4h4.6a14.7 14.7 0 0 1 0 4zm.3 5.6c.6-1.1 1.1-2.3 1.4-3.6h2.9a8 8 0 0 1-4.3 3.6zm1.7-5.6a16.5 16.5 0 0 0 0-4h3.4a8 8 0 0 1 0 4z"/></svg>
        info@yourwebsite.com
      </li>
      <li>
        <svg viewBox="0 0 24 24" aria-hidden="true"><path d="M3 9l9-6 9 6v11a1 1 0 0 1-1 1H4a1 1 0 0 1-1-1zm2 1.2V19h14v-8.8l-7 4.6z"/></svg>
        www.yourwebsite.com
      </li>
    </ul>
    <p class="address">1840 Elmcrest Ave. Suite 300 Dallas, TX 75201</p>
  </section>
</main>
</body>
</html>
```